RWT Fittings Ltd Business Cards

We need a business card with our business logo. We provide window and door installations on high-rises in west coast British Colombia, Canada.

I would like my business information and details on one side of the card, and the other side the company name with logo

Target Market(s)

General Contractors

Industry/Entity Type

Construction

Contact Information for Business Card

one side i want my company name and logo in the dark theme logo that i provided

Requirements
Must have
• Marco Peltieri, 16045518293, RWTFittings@mailbox-demo.com, 1407-5194 Linden Row Burnaby BC, V5H 2K9, Owner & Manager

```html
<!DOCTYPE html>
<html lang="en">
<head>
<meta charset="UTF-8">
<title>RWT Fittings Ltd – Business Cards</title>
<link rel="stylesheet" href="https://fonts.googleapis.com/css2?family=Montserrat:wght@700;800&family=Poppins:wght@300;400;600&display=swap">
<style>
  :root {
    --stage: #1b1b1c;
    --card-light: #ffffff;
    --card-dark-top: #3a3634;
    --card-dark-bottom: #1f1d1c;
    --brand-blue: #29a8e0;
    --brand-cyan: #31c6f2;
    --text-grey: #6e6e6e;
  }
  * { margin: 0; padding: 0; box-sizing: border-box; }
  html, body {
    width: 1200px;
    height: 963px;
    overflow: hidden;
    background: var(--stage);
    font-family: "Poppins", sans-serif;
  }
  .canvas {
    width: 1200px;
    height: 963px;
    display: flex;
    align-items: center;
    justify-content: center;
    gap: 40px;
  }
  .card {
    position: relative;
    width: 540px;
    height: 309px;
    border-radius: 16px;
    overflow: hidden;
    box-shadow: 0 14px 34px rgba(0,0,0,0.55);
  }

  /* Front: details side */
  .card--front { background: var(--card-light); }
  .front-wordmark {
    position: absolute;
    top: 38px;
    left: 108px;
    display: flex;
    align-items: center;
    gap: 10px;
    font-weight: 600;
    font-size: 30px;
    color: var(--brand-blue);
    letter-spacing: 0.5px;
  }
  .wordmark-square {
    width: 22px;
    height: 22px;
    background: var(--brand-blue);
  }
  .contact-list {
    position: absolute;
    left: 40px;
    top: 150px;
    list-style: none;
    color: var(--text-grey);
    font-size: 12.5px;
    line-height: 1.45;
    font-weight: 400;
  }
  .contact-list .address { margin-bottom: 6px; }
  .contact-list li { display: flex; align-items: center; gap: 7px; }
  .contact-list svg { width: 12px; height: 12px; flex: none; }
  .holder {
    position: absolute;
    right: 40px;
    top: 120px;
    text-align: right;
  }
  .holder-name {
    font-family: "Montserrat", sans-serif;
    font-weight: 800;
    font-size: 21px;
    color: var(--brand-blue);
    letter-spacing: 1px;
  }
  .holder-role {
    font-size: 13px;
    font-weight: 300;
    color: var(--text-grey);
    letter-spacing: 1px;
  }
  .front-accent {
    position: absolute;
    right: 70px;
    bottom: 34px;
    width: 92px;
    height: 92px;
    background: var(--brand-blue);
  }

  /* Back: brand side */
  .card--back {
    background: linear-gradient(135deg, var(--card-dark-top), var(--card-dark-bottom));
    display: flex;
    align-items: center;
    justify-content: center;
  }
  .back-wordmark {
    display: flex;
    align-items: center;
    gap: 14px;
    font-weight: 600;
    font-size: 40px;
    color: var(--brand-cyan);
    letter-spacing: 0.5px;
  }
  .back-wordmark .wordmark-square {
    width: 30px;
    height: 30px;
    background: var(--brand-cyan);
  }
</style>
</head>
<body>
<main class="canvas">
  <section class="card card--front" aria-label="Business card front">
    <div class="front-wordmark"><span class="wordmark-square"></span>RWT Fittings Ltd</div>

    <ul class="contact-list">
      <li class="address">1407-5194 Linden Row<br>Burnaby BC, V5H 2K9</li>
      <li>
        <svg viewBox="0 0 24 24" aria-hidden="true"><path fill="var(--brand-blue)" d="M6.6 10.8a15 15 0 0 0 6.6 6.6l2.2-2.2a1 1 0 0 1 1-.25 11.4 11.4 0 0 0 3.6.57 1 1 0 0 1 1 1V20a1 1 0 0 1-1 1A17 17 0 0 1 3 4a1 1 0 0 1 1-1h3.5a1 1 0 0 1 1 1c0 1.25.2 2.45.57 3.57a1 1 0 0 1-.25 1z"/></svg>
        604-551-8293
      </li>
      <li>
        <svg viewBox="0 0 24 24" aria-hidden="true"><rect x="2" y="5" width="20" height="14" rx="1.5" fill="none" stroke="var(--brand-blue)" stroke-width="2"/><path d="M3 6l9 7 9-7" fill="none" stroke="var(--brand-blue)" stroke-width="2"/></svg>
        RWTFittings@mailbox-demo.com
      </li>
      <li>
        <svg viewBox="0 0 24 24" aria-hidden="true"><circle cx="12" cy="12" r="10" fill="var(--brand-blue)"/><path d="M2 12h20M12 2c3 3 3 17 0 20M12 2c-3 3-3 17 0 20" fill="none" stroke="#fff" stroke-width="1.3"/></svg>
        www.rwtfittings-demo.com
      </li>
    </ul>

    <div class="holder">
      <div class="holder-name">MARCO PELTIERI</div>
      <div class="holder-role">Owner &amp; Manager</div>
    </div>

    <div class="front-accent" aria-hidden="true"></div>
  </section>

  <section class="card card--back" aria-label="Business card back">
    <div class="back-wordmark"><span class="wordmark-square"></span>RWT Fittings Ltd</div>
  </section>
</main>
</body>
</html>
```